Brindlewood Home & Commercial Services, Inc.

I need a facebook design for our commercial repair/maintenance company based in Austin, TX. We offer many commercial services:plumbing, HVAC, Carpet/Air duct cleaning, Fire and water restoration, and general maintenance services
Our customer base includes commercial government organizations as NMDX and Fort Tellison. We serve as the general contractor for these organizations and can handle any scope of work. ie flooring install, drywall, asbestos abatement, and mold removal.
We need a facebook design that communicates to our customer that we strive in customer satisfaction and pricing.
Updates
Logo uploaded. I will also upload photos for some job that have been completed.
I don't have images of our employees actively doing a job. I do have before and after picture that intend to post after fb cover is created.
I like the designs. I will sit with my husband tonight to brainstorm or select a design. Keep submitting, please.
Target Market(s)
Commercial
Industry/Entity Type
Government
Look and feel

```html
<!DOCTYPE html>
<html lang="en">
<head>
<meta charset="utf-8">
<title>Brindlewood Home &amp; Commercial Services — Cover</title>
<link rel="stylesheet" href="https://fonts.googleapis.com/css2?family=PT+Serif:wght@400;700&display=swap">
<style>
  :root {
    --bg: #f4f6f3;
    --sage-pale: #a9b3a2;
    --sage-light: #9eaa96;
    --sage-mid: #7f8f77;
    --sage-deep: #5e7157;
    --forest: #3d5437;
    --brand: #2f4a2b;
  }
  html, body {
    margin: 0;
    padding: 0;
    width: 1200px;
    height: 444px;
    overflow: hidden;
    background: var(--bg);
  }
  .cover {
    display: block;
    width: 1200px;
    height: 444px;
  }
  .word {
    font-family: "PT Serif", Georgia, serif;
    font-weight: 400;
  }
  .pale { fill: var(--sage-pale); }
  .light { fill: var(--sage-light); }
  .mid { fill: var(--sage-mid); }
  .deep { fill: var(--sage-deep); }
  .forest { fill: var(--forest); }
  .brand-name {
    font-family: "PT Serif", Georgia, serif;
    font-weight: 700;
    fill: var(--brand);
  }
  .brand-mark { fill: var(--brand); }
</style>
</head>
<body>
<svg class="cover" viewBox="0 0 1200 444" xmlns="http://www.w3.org/2000/svg" role="img" aria-label="Word cloud of services offered by Brindlewood Home &amp; Commercial Services">
  <rect width="1200" height="444" fill="var(--bg)"/>

  <g class="word-cloud">
    <text class="word light" x="423" y="40" font-size="42" textLength="215" lengthAdjust="spacingAndGlyphs">contractor</text>
    <text class="word light" x="533" y="73" font-size="37" textLength="228" lengthAdjust="spacingAndGlyphs">restoration .</text>
    <text class="word mid" x="819" y="71" font-size="38" textLength="108" lengthAdjust="spacingAndGlyphs">water</text>
    <text class="word light" x="705" y="110" font-size="39" textLength="258" lengthAdjust="spacingAndGlyphs">maintenance</text>

    <text class="word light" x="-4" y="155" font-size="205" textLength="455" lengthAdjust="spacingAndGlyphs">repair</text>

    <text class="word forest" x="458" y="152" font-size="42" textLength="202" lengthAdjust="spacingAndGlyphs">plumbing</text>
    <text class="word light" x="682" y="158" font-size="87" textLength="452" lengthAdjust="spacingAndGlyphs">guaranteed</text>

    <text class="word forest" x="226" y="206" font-size="36" textLength="56" lengthAdjust="spacingAndGlyphs">air</text>
    <text class="word forest" x="494" y="193" font-size="40" textLength="172" lengthAdjust="spacingAndGlyphs">cleaning</text>
    <text class="word deep" x="743" y="198" font-size="40" textLength="104" lengthAdjust="spacingAndGlyphs">mold</text>
    <text class="word deep" x="963" y="198" font-size="40" textLength="109" lengthAdjust="spacingAndGlyphs">ducts</text>

    <text class="word deep" x="299" y="230" font-size="38" textLength="160" lengthAdjust="spacingAndGlyphs">flooring</text>
    <text class="word pale" x="183" y="262" font-size="35" textLength="170" lengthAdjust="spacingAndGlyphs">asbestos</text>
    <text class="word pale" x="413" y="286" font-size="40" textLength="137" lengthAdjust="spacingAndGlyphs">HVAC</text>

    <text class="word deep" x="578" y="279" font-size="148" textLength="622" lengthAdjust="spacingAndGlyphs">services</text>

    <text class="word forest" x="630" y="331" font-size="40" textLength="256" lengthAdjust="spacingAndGlyphs">construction</text>
  </g>

  <g class="brand">
    <rect class="brand-mark" x="284" y="352" width="28" height="28"/>
    <text class="brand-name" x="324" y="378" font-size="36">Brindlewood</text>
    <text class="brand-name" x="324" y="410" font-size="20">Home &amp; Commercial Services</text>
  </g>
</svg>
</body>
</html>
```